Dentistry Office

We want a new design for a Dentist's office website.

The theme is: "We provide high quality, state-of-the-art, dental care in a comfortable, caring environment."

The site currently has a menu on the left of the page with about 40 items on it. There is a great deal of textual content on each page, plus several illustrations.

We want to do this using CSS, so we need specifications in the CSS for all possible elements. The CSS needs to be named in a logical manner for easy use.

Every dentist on the planet seems to use lots of Flash. We don't want to because it is so distracting. We are looking for an elegant solution targeting 24-55 age group, but not excluding anyone.

The following (from another dentist's site) can give you a taste of what we want to communicate on the site:

"After 20 years of teaching dentists how to refine their technique and many years of writing textbooks, I currently devote my time to my office and the hands-on practice of dentistry. I'd like to welcome you personally to my dental practice, and I invite you to meet my highly experienced team of professionals.

"We have offered complete dental care of the highest quality since 1978. We provide Preventive Services, Tooth Whitening and Cosmetic Dentistry for a beautiful smile, Endodontics (root canal treatment) to treat painful teeth, Sedation Dentistry so you can relax, and Dental Implants to restore what is missing. We offer total care.

"Our approach to your health is simple: We use our education, experience and dedication to provide every patient with superior dental care.

"This passion for excellence is not just a goal, but a standard every member of our team holds.

"We also pride ourselves with our state of the art procedures, training and technology. This includes creating a beautiful smile using techniques that preserve as much of the original tooth as possible.

"Our abilities are renowned throughout the dental profession and I hope if you have any questions you will contact us by an e-mail note, by phone or just by dropping by."

Keep in mind the screen shape and dimensions. Your design needs to work in the normal screen proportions, regardless of how it looks when you post it here. Scrolling is OK, but the first impression needs to work.
Updates

Keep in mind that there will be about 250 words, or more, on each page.

Competitors web sites:

http://www.brindlecovedentist.example/

http://www.brindlecovedentalcare.example/

http://www.grinsbymarlowvaledental.example/

http://www.tenbyfamilydentalcare.example/

http://www.quelmardental.example/

http://www.dovrinadental.example/

We need to compete with these.

Target Market(s)

Generally adults seeking the most experienced and comfortable-to-be-with dentist.

Industry/Entity Type

Training

Requirements
Must have
• Must stand apart from other dentists.
• Must be elegant.
• Must have a horizontal menu structure across all columns, NOT a vertical that requires scrolling, no popout, pop down, etc. menus.
• We are looking for something special.
• Do not waste your time or ours putting up templates and things you have used before.
• Personally, I do not see how someone outside the US can understand the northern California dental market. But you are welcome to try.
Should not have
• Flash or graphics that move
• The look of a template
• Folksy fonts
• Looks like you used it 20 times before

```html
<!DOCTYPE html>
<html lang="en">
<head>
<meta charset="utf-8">
<title>Brindle Cove Dentist Owen Tessler, DDS, FAGD</title>
<link rel="stylesheet" href="https://fonts.googleapis.com/css2?family=PT+Sans:wght@400;700&family=Arimo:wght@400;700&display=swap">
<style>
  :root {
    --slate-dark: #4b4f5c;
    --slate: #626775;
    --slate-light: #7d8290;
    --page-bg: #f3f4f5;
    --panel-bg: #e9eaec;
    --panel-line: #c9cbd0;
    --ink: #3c3f45;
    --ink-soft: #55585e;
    --heading: #3f4a4f;
    --white: #ffffff;
    --accent-orange: #f0a21c;
    --accent-blue: #2f7fd0;
    --accent-red: #c8352c;
  }
  * { box-sizing: border-box; margin: 0; padding: 0; }
  html, body { width: 819px; height: 1200px; overflow: hidden; background: var(--page-bg); }
  body { font-family: "Arimo", Arial, sans-serif; color: var(--ink); }
  ul { list-style: none; }

  .page {
    position: relative; width: 830px; height: 1214px;
    transform: scale(0.98675, 0.98847); transform-origin: 0 0;
    background: var(--page-bg);
  }
  .abs { position: absolute; }

  /* Header */
  .site-header {
    left: 0; top: 0; width: 830px; height: 54px;
    background: linear-gradient(#6a6e7c, var(--slate-dark));
    color: var(--white); text-align: center;
    font-family: "PT Sans", sans-serif; font-size: 29px; line-height: 50px; letter-spacing: .5px;
  }

  /* Hero */
  .hero {
    left: 3px; top: 54px; width: 824px; height: 243px;
    background: linear-gradient(90deg, #e6eaee, #f4f6f8 40%, #dfe4e9);
  }
  .hero-photo {
    left: 345px; top: 0; width: 372px; height: 228px;
    background: linear-gradient(135deg, #d9c3a6, #b88f6c 45%, #8fa8bf 75%, #e9eef2);
  }
  .main-nav {
    left: 87px; top: 83px; width: 174px; height: 214px;
    background: linear-gradient(#5f6371, #4f5361);
    box-shadow: 2px 3px 5px rgba(0,0,0,.25);
    padding-top: 11px;
  }
  .main-nav li {
    height: 27px; line-height: 25px; padding-left: 20px;
    color: var(--white); font-size: 11px; font-weight: 700; letter-spacing: .3px;
    border-bottom: 1px solid #777b87;
  }
  .main-nav li:last-child { border-bottom: 0; }

  /* Appointment line */
  .call-line { left: 405px; top: 290px; height: 32px; display: flex; align-items: center; gap: 8px; }
  .call-line span { font-family: "PT Sans", sans-serif; font-size: 16px; color: var(--ink); letter-spacing: .4px; }

  /* Topic menu */
  .topic-menu {
    left: 70px; top: 327px; width: 695px; height: 205px;
    background: var(--panel-bg); border: 1px solid var(--panel-line);
  }
  .topic-menu-bar { height: 23px; background: linear-gradient(#6c707e, var(--slate-dark)); }
  .topic-col { position: absolute; top: 0; }
  .topic-col h3 {
    height: 23px; line-height: 24px; color: var(--white);
    font-size: 11.5px; font-weight: 700; letter-spacing: .6px;
  }
  .topic-col ul { margin-top: 8px; }
  .topic-col li { font-size: 10px; line-height: 17px; color: var(--ink); white-space: nowrap; }
  .topic-col li.is-active {
    background: var(--slate-light); color: var(--white);
    margin-left: -9px; padding-left: 9px; width: 120px;
  }

  /* Welcome */
  .section-title { font-family: "PT Sans", sans-serif; font-size: 15px; color: var(--heading); letter-spacing: .3px; }
  .welcome-title { left: 82px; top: 538px; }
  .welcome-text {
    left: 82px; top: 565px; width: 494px;
    font-size: 9.6px; line-height: 15.6px; color: var(--ink-soft);
  }
  .welcome-photo {
    left: 587px; top: 555px; width: 164px; height: 122px;
    border: 2px solid #d3d5d8;
    background: linear-gradient(#a9c48a, #6f8a5a 45%, #8b7566 70%, #7b7f7e);
  }
  .btn-pill {
    left: 493px; top: 658px; width: 83px; height: 18px;
    background: linear-gradient(#8a8f9b, var(--slate)); border-radius: 3px;
    color: var(--white); font-size: 9.5px; font-weight: 700; line-height: 18px; text-align: center;
  }

  /* Services */
  .services-title { left: 87px; top: 671px; }
  .services-list { left: 120px; top: 710px; }
  .services-list li {
    display: flex; align-items: center; gap: 9px;
    height: 20.4px; font-size: 9.6px; color: var(--ink-soft);
  }

  /* Side tabs */
  .side-tab {
    left: 70px; width: 192px; height: 31px;
    background: linear-gradient(#8a8e9a, var(--slate));
    border-radius: 4px; color: var(--white);
    font-family: "PT Sans", sans-serif; font-size: 15px; line-height: 31px; padding-left: 16px;
  }
  .side-tab svg { position: absolute; right: 6px; top: -10px; }
  .tab-hours { top: 930px; }
  .tab-stay { top: 990px; }
  .tab-call { top: 1052px; border-radius: 4px 4px 0 0; }
  .call-note {
    left: 70px; top: 1083px; width: 192px; height: 48px;
    background: var(--white); border-radius: 0 0 4px 4px;
    padding: 4px 6px; font-size: 9.5px; line-height: 13px; color: var(--ink);
  }
  .call-note strong { letter-spacing: .5px; }

  /* Offer */
  .offer-title {
    left: 283px; top: 927px; width: 234px; text-align: center;
    font-family: "PT Sans", sans-serif; font-size: 14.5px; line-height: 19px; color: var(--ink);
  }
  .offer-photo {
    left: 283px; top: 972px; width: 234px; height: 98px;
    border: 2px solid #9aa0ab; border-radius: 4px;
    background: linear-gradient(90deg, #e7b79a, #c9826a 35%, #6a4fb0 55%, #e08a1c 75%, #f2c070);
  }
  .offer-price {
    left: 283px; top: 1075px; width: 234px; text-align: center;
    font-family: "PT Sans", sans-serif; font-size: 23px; font-weight: 700; color: var(--heading); letter-spacing: .5px;
  }
  .offer-link { left: 447px; top: 1120px; font-size: 10px; color: var(--ink); letter-spacing: .4px; }

  /* Map */
  .map-title { left: 535px; top: 905px; font-family: "PT Sans", sans-serif; font-size: 15px; color: var(--ink); }
  .map-area {
    left: 535px; top: 927px; width: 230px; height: 207px;
    border: 1px solid #c2c4c8;
    background: linear-gradient(135deg, #e9e8e4, #dcdbd6);
  }

  /* Footer */
  .site-footer {
    left: 3px; top: 1155px; width: 824px; height: 59px;
    background: repeating-linear-gradient(45deg, #5a5e6b 0 2px, #525663 2px 4px);
    color: var(--white); font-size: 9.5px;
  }
  .footer-links { position: absolute; left: 82px; top: 10px; }
  .footer-copy { position: absolute; left: 82px; top: 34px; }
  .top-tab {
    position: absolute; left: 685px; top: 0; width: 47px; height: 23px;
    background: var(--white); color: var(--accent-blue); opacity: .9;
    font-size: 11px; line-height: 23px; text-align: center;
  }
</style>
</head>
<body>
<div class="page">

  <header class="site-header abs">Brindle Cove Dentist Owen Tessler, DDS, FAGD</header>

  <section class="hero abs">
    <div class="hero-photo abs" role="img" aria-label="Smiling family of four lying together on a bright floor"></div>
  </section>

  <nav class="main-nav abs">
    <ul>
      <li>Home</li>
      <li>Why we are differnt</li>
      <li>Technologies we offer</li>
      <li>Meet Dr.Tessler</li>
      <li>Our Staff</li>
      <li>Contact Us</li>
      <li>Links</li>
    </ul>
  </nav>

  <div class="call-line abs">
    <svg width="56" height="32" viewBox="0 0 56 32" aria-hidden="true">
      <path d="M4 10 Q28 -2 52 10 L50 15 L40 13 L38 8 Q28 5 18 8 L16 13 L6 15 Z" fill="#222"/>
      <path d="M14 14 L42 14 L48 30 L8 30 Z" fill="#2b2b2b"/>
      <circle cx="28" cy="21" r="5" fill="#555"/>
      <ellipse cx="28" cy="31" rx="24" ry="1.5" fill="#bbb"/>
    </svg>
    <span>Call for Appointments: (555) 014-2290.</span>
  </div>

  <section class="topic-menu abs">
    <div class="topic-menu-bar"></div>
    <div class="topic-col" style="left:13px">
      <h3>EDUCATION</h3>
      <ul>
        <li>Emergency Dental Care</li>
        <li class="is-active">Your Mouth</li>
        <li>Your Tooth</li>
        <li>Cracked Tooth?</li>
        <li>Missing a Tooth?</li>
        <li>Sensitive Teeth</li>
        <li>Dry MouthTooth</li>
        <li>GrindingSleep</li>
        <li>Dentistry</li>
        <li>Videos</li>
      </ul>
    </div>
    <div class="topic-col" style="left:141px">
      <h3>PREVENTATIVE</h3>
      <ul>
        <li>What is Preventive Care?</li>
        <li>Taking Care of Your Teeth</li>
        <li>Eating Right</li>
        <li>Dental Check-Ups</li>
        <li>Sealants</li>
        <li>Periodontal Disease</li>
        <li>Kicking the Habit</li>
        <li>Night Guards</li>
        <li>Dental X-Rays</li>
        <li>Antibiotics with Treatment</li>
      </ul>
    </div>
    <div class="topic-col" style="left:287px">
      <h3>COSMETICS</h3>
      <ul>
        <li>Cosmetic Dentistry</li>
        <li>Bleaching and Whitening</li>
        <li>Cosmetic Bonding</li>
        <li>Esthetic Veneers</li>
        <li>Tooth Shaping</li>
      </ul>
    </div>
    <div class="topic-col" style="left:419px">
      <h3>RESTORATIONS</h3>
      <ul>
        <li>Crowns/Caps: Each Step</li>
        <li>CMBRs</li>
        <li>Porcelain Bridges</li>
        <li>Bonded Dental Bridges</li>
        <li>Gold Restorations</li>
        <li>Implants</li>
        <li>Treating CrackedTeeth</li>
        <li>Periodontal (gum)</li>
        <li>Treatment</li>
      </ul>
    </div>
    <div class="topic-col" style="left:557px">
      <h3>VISITING OUR OFFICE</h3>
      <ul>
        <li>Where to Stay</li>
        <li>First Visit / Map</li>
        <li>Financial Policy</li>
        <li>Dental Insurance</li>
      </ul>
    </div>
  </section>

  <h2 class="section-title welcome-title abs">Welcome</h2>
  <p class="welcome-text abs">Lorem ipsum dolor sit amet, consectetuer adipiscing elit. Aenean commodo ligula eget dolor. Aenean massa. Cum sociis natoque penatibus et magnis dis parturient montes, nascetur ridiculus mus. Doneuam felis, ultricies nec, pellentesque eu, pretium quis, sem. Nulla consequat massa quis enim. Donec pede justo, fringilla vel, aliquet nec, vulputate eget, arcu. In enim justo, rhoncus ut, imperdiet a, venenatis vitae, justo.massa quis enim. Donec pede justo, &nbsp;pretium quis, sem. Nulla consequat massa quis enim. Donec pede justo, fringilla vel, In enim justo, rhoncus ut, imperdiet a, venenatis vitae, justo.massa quis enim. Donec pede justo, &nbsp;pretium quis, sem. Nulla consequat massa quis enim. Donec pede justo, fringilla vel,</p>
  <div class="welcome-photo abs" role="img" aria-label="Stone and wood dental office building among green trees"></div>
  <div class="btn-pill abs">Learn more &#9656;&#9656;</div>

  <h2 class="section-title services-title abs">Dr. Tessler Provides</h2>
  <ul class="services-list abs">
    <li><svg width="10" height="10" viewBox="0 0 10 10" aria-hidden="true"><path d="M1 5 L4 8 L9 1" stroke="#5a5e68" stroke-width="2" fill="none"/></svg>General dentistry—oral hygiene, cavity detection and repair, crowns.</li>
    <li><svg width="10" height="10" viewBox="0 0 10 10" aria-hidden="true"><path d="M1 5 L4 8 L9 1" stroke="#5a5e68" stroke-width="2" fill="none"/></svg>Cosmetic/restorative dentistry—broken or misshapen teeth, crooked smiles, unsightly gaps</li>
    <li><svg width="10" height="10" viewBox="0 0 10 10" aria-hidden="true"><path d="M1 5 L4 8 L9 1" stroke="#5a5e68" stroke-width="2" fill="none"/></svg>Non-metal fillings—nontoxic, durable tooth-colored resin fillings that are proven to provide better results</li>
    <li><svg width="10" height="10" viewBox="0 0 10 10" aria-hidden="true"><path d="M1 5 L4 8 L9 1" stroke="#5a5e68" stroke-width="2" fill="none"/></svg>Tooth shaping—extending, shortening or otherwise reshaping teeth for improved esthetics</li>
    <li><svg width="10" height="10" viewBox="0 0 10 10" aria-hidden="true"><path d="M1 5 L4 8 L9 1" stroke="#5a5e68" stroke-width="2" fill="none"/></svg>Complete smile make-over's—resin veneers that reshape the whole mouth while preserving natural teeth</li>
    <li><svg width="10" height="10" viewBox="0 0 10 10" aria-hidden="true"><path d="M1 5 L4 8 L9 1" stroke="#5a5e68" stroke-width="2" fill="none"/></svg>Tooth whitening—at-home bleaching options to make teeth appear years younger</li>
    <li><svg width="10" height="10" viewBox="0 0 10 10" aria-hidden="true"><path d="M1 5 L4 8 L9 1" stroke="#5a5e68" stroke-width="2" fill="none"/></svg>Laser Dentistry, Sleep Dentistry, and Implant Dentistry with the Finest and Latest Equipment and Materials.</li>
    <li><svg width="10" height="10" viewBox="0 0 10 10" aria-hidden="true"><path d="M1 5 L4 8 L9 1" stroke="#5a5e68" stroke-width="2" fill="none"/></svg>Dental Implants to replace missing teeth.</li>
    <li><svg width="10" height="10" viewBox="0 0 10 10" aria-hidden="true"><path d="M1 5 L4 8 L9 1" stroke="#5a5e68" stroke-width="2" fill="none"/></svg>Sedation Dentistry so you can be relaxed.</li>
  </ul>

  <div class="side-tab tab-hours abs">Office Hours
    <svg width="34" height="34" viewBox="0 0 34 34" aria-hidden="true">
      <circle cx="17" cy="17" r="15" fill="#fff" stroke="var(--accent-orange)" stroke-width="3"/>
      <path d="M17 8 V17 H24" stroke="#333" stroke-width="2" fill="none"/>
    </svg>
  </div>
  <div class="side-tab tab-stay abs">Where to stay?
    <svg width="34" height="34" viewBox="0 0 34 34" aria-hidden="true">
      <circle cx="17" cy="17" r="15" fill="var(--accent-blue)" stroke="#fff" stroke-width="2"/>
      <text x="17" y="24" text-anchor="middle" font-family="Arimo, sans-serif" font-size="19" font-weight="700" fill="#fff">?</text>
    </svg>
  </div>
  <div class="side-tab tab-call abs">Please call
    <svg width="34" height="34" viewBox="0 0 34 34" aria-hidden="true">
      <path d="M8 6 Q4 10 8 18 Q14 28 24 30 Q29 30 30 26 L24 21 L20 24 Q14 20 12 14 L15 10 Z" fill="var(--accent-red)"/>
    </svg>
  </div>
  <p class="call-note abs">contact us outside office hours for an emergency, please call at<br><strong>(555) 018-3371.</strong></p>

  <h2 class="offer-title abs">We offer an Initial Patient Examination X-rays and Cleaning</h2>
  <div class="offer-photo abs" role="img" aria-label="Dentist using a curing light on a patient's teeth"></div>
  <p class="offer-price abs">for $79.00.</p>
  <p class="offer-link abs">Learn More &nbsp;&#9656;&#9656;</p>

  <h2 class="map-title abs">Map to Office</h2>
  <div class="map-area abs" role="img" aria-label="Street map showing the route to the office"></div>

  <footer class="site-footer abs">
    <p class="footer-links">Brindle Cove Dentist • Tell A Friend • Privacy &amp; Legal • Dental Resources • New Patient Forms</p>
    <p class="footer-copy">Copyright © 2009. All Rights Reserved</p>
    <div class="top-tab">Top</div>
  </footer>

</div>
</body>
</html>
```